Law Firm Header Revision

Task: Redesign my law firm Word document header (modern, succinct, logo-first, easy address updates)

I need you to revise and modernize my Microsoft Word document header for Law Office of Bram Holcott, PLLC. The result should look professional and clean on letters (including Letters of Protection), with the logo as the main focus and the text kept succinct.

Goals:
1. Create a modern, minimal header that feels premium and uncluttered.
Make the logo the most visually dominant element.
Reduce the visual weight of the contact/address block so it doesn’t distract from the document.
Make the address easy to change later (I’m moving offices soon) while keeping the same header design.

2. Content to include (keep all info accurate):
Law Office of Bram Holcott, PLLC
615 Pemberly St. Ste #300-214, Houston, TX 77002
Office: 832.555.0143
Direct: 713.555.0187
Fax: 832.555.0129
Bholcottlaw.com

3. Layout requirements:
Provide 3 header style options:
Logo left + contact info right
Centered logo + single concise contact line below
Logo left + firm name prominent + minimal contact line
The primary line near the logo should be minimal (preferably website + main office phone).
The address should be easy to update in one place without redesigning the header. Prefer either:
Move the full address to the footer, or
Put the address in a single dedicated line/block so I can edit it once and keep the layout unchanged.
4. Build constraints:
Must be achievable using standard Microsoft Word tools only (header/footer, tables, alignment, fonts, spacing). No advanced graphics software.
Provide exact header text, plus step-by-step Word instructions for each option:
Font recommendations + sizes
Alignment
Spacing
Table setup (if used)
How to keep it consistent across pages

5. Deliverable:
For each of the 3 options, provide:
The exact header content (with line breaks)
Formatting specs (fonts, sizes, spacing)
Word build steps so I can recreate it reliably and keep the logo as the focal point.

```html
<!DOCTYPE html>
<html lang="en">
<head>
<meta charset="utf-8">
<title>Bram Holcott Law – Letterhead Options</title>
<link href="https://fonts.googleapis.com/css2?family=Inter:wght@400;500;600&display=swap" rel="stylesheet">
<style>
  :root {
    --stage: #9d9ea2;
    --paper: #ffffff;
    --navy: #0f1e33;
    --ink: #1b2433;
    --rule: #8a8d93;
    --band: #e8e9ec;
  }
  * { box-sizing: border-box; margin: 0; padding: 0; }
  html, body { width: 1200px; height: 557px; overflow: hidden; }
  body {
    background: var(--stage);
    font-family: "Inter", Arial, sans-serif;
    color: var(--ink);
    position: relative;
  }
  .sheet {
    position: absolute;
    top: 62px;
    width: 339px;
    height: 438px;
    background: var(--paper);
    box-shadow: 0 6px 18px rgba(0,0,0,0.18);
    overflow: hidden;
  }
  .sheet--left-contact { left: 55px; }
  .sheet--stacked-contact { left: 420px; }
  .sheet--centered { left: 788px; }

  .header { position: absolute; left: 0; right: 0; top: 0; border-bottom: 0.6px solid var(--rule); }
  .header--compact { height: 50px; }
  .header--tall { height: 74px; }

  .brand { position: absolute; display: flex; align-items: center; gap: 4px; color: var(--navy); }
  .brand__mark { background: var(--navy); flex: none; }
  .brand__name { font-weight: 600; text-transform: uppercase; line-height: 1; text-align: center; color: var(--navy); }
  .brand__name span { display: block; }
  .brand--side { left: 9px; top: 9px; }
  .brand--side .brand__mark { width: 26px; height: 28px; }
  .brand--side .brand__name { font-size: 13px; letter-spacing: -0.2px; }
  .brand--side .brand__sub { font-size: 7px; letter-spacing: 2.5px; margin-top: 3px; }
  .brand--center { left: 50%; top: 10px; transform: translateX(-50%); gap: 5px; }
  .brand--center .brand__mark { width: 30px; height: 33px; }
  .brand--center .brand__name { font-size: 16px; letter-spacing: -0.2px; }
  .brand--center .brand__sub { font-size: 8px; letter-spacing: 3px; margin-top: 4px; }

  .contact { position: absolute; color: var(--ink); white-space: nowrap; }
  .contact__item { display: flex; align-items: center; gap: 5px; line-height: 1; }
  .icon { width: 7px; height: 7px; fill: var(--navy); flex: none; }

  .contact--right-large { left: 253px; top: 10px; font-size: 9.2px; }
  .contact--right-large .contact__item { margin-bottom: 9px; }
  .contact--right-large .icon { width: 7px; height: 7px; }

  .contact--stacked { right: 8px; top: 9px; font-size: 7.4px; text-align: right; }
  .contact--stacked .contact__item { justify-content: flex-end; margin-bottom: 3.2px; }
  .contact--stacked .icon { width: 6px; height: 6px; }

  .contact--line { left: 0; right: 0; top: 54px; display: flex; justify-content: center; gap: 7px; font-size: 8px; }
  .contact--line .icon { width: 6.5px; height: 6.5px; }

  .footer { position: absolute; left: 0; right: 0; bottom: 0; height: 22px; background: var(--band); }
  .footer__address {
    position: absolute; left: 6px; top: 0; height: 22px; width: 250px;
    display: flex; align-items: center; gap: 3px; font-size: 5.7px; white-space: nowrap; color: var(--ink);
  }
  .footer__address .icon { width: 5px; height: 5px; }
  .footer__address .gap { width: 1px; }
  .footer__divider { position: absolute; left: 258px; top: 0; width: 1px; height: 22px; background: var(--paper); }
  .footer__label {
    position: absolute; left: 263px; top: 0; height: 22px; display: flex; align-items: center;
    font-size: 5.1px; letter-spacing: 0.1px; text-transform: uppercase; color: var(--ink);
  }
  .page-number {
    position: absolute; right: -3px; bottom: -4px; width: 15px; height: 15px; border-radius: 50%;
    background: var(--navy); color: #fff; font-size: 5px; display: flex; align-items: center; justify-content: center;
    padding: 0 2px 2px 0;
  }
</style>
</head>
<body>
<svg width="0" height="0" style="position:absolute">
  <defs>
    <symbol id="i-phone" viewBox="0 0 24 24"><path d="M6.6 10.8a15.1 15.1 0 0 0 6.6 6.6l2.2-2.2c.3-.3.7-.4 1-.2 1.1.4 2.3.6 3.6.6.6 0 1 .4 1 1V20c0 .6-.4 1-1 1A17 17 0 0 1 3 4c0-.6.4-1 1-1h3.5c.6 0 1 .4 1 1 0 1.3.2 2.5.6 3.6.1.3 0 .7-.2 1z"/></symbol>
    <symbol id="i-globe" viewBox="0 0 24 24"><path d="M12 2a10 10 0 1 0 0 20 10 10 0 0 0 0-20zm7.9 9h-3.9a15.6 15.6 0 0 0-1.4-6.4A8 8 0 0 1 19.9 11zM12 4c1 1.3 1.9 3.9 2 7h-4c.1-3.1 1-5.7 2-7zM9.4 4.6A15.6 15.6 0 0 0 8 11H4.1a8 8 0 0 1 5.3-6.4zM4.1 13H8c.1 2.4.6 4.6 1.4 6.4A8 8 0 0 1 4.1 13zM12 20c-1-1.3-1.9-3.9-2-7h4c-.1 3.1-1 5.7-2 7zm2.6-.6c.8-1.8 1.3-4 1.4-6.4h3.9a8 8 0 0 1-5.3 6.4z"/></symbol>
    <symbol id="i-pin" viewBox="0 0 24 24"><path d="M12 2a7 7 0 0 0-7 7c0 5.2 7 13 7 13s7-7.8 7-13a7 7 0 0 0-7-7zm0 9.5a2.5 2.5 0 1 1 0-5 2.5 2.5 0 0 1 0 5z"/></symbol>
    <symbol id="i-fax" viewBox="0 0 24 24"><path d="M6 2h12v5H6zM4 8h16a2 2 0 0 1 2 2v7h-4v5H6v-5H2v-7a2 2 0 0 1 2-2zm4 8v4h8v-4z"/></symbol>
    <symbol id="i-office" viewBox="0 0 24 24"><path d="M12 2 2 7v2h20V7zM4 11h3v7H4zm6.5 0h3v7h-3zM17 11h3v7h-3zM2 20h20v2H2z"/></symbol>
  </defs>
</svg>

<!-- Option 1: logo left, contact right -->
<section class="sheet sheet--left-contact">
  <header class="header header--compact">
    <div class="brand brand--side">
      <div class="brand__mark"></div>
      <div class="brand__name"><span>Bram Holcott</span><span class="brand__sub">Law</span></div>
    </div>
    <div class="contact contact--right-large">
      <div class="contact__item"><svg class="icon"><use href="#i-phone"/></svg><span>832.555.0143</span></div>
      <div class="contact__item"><svg class="icon"><use href="#i-globe"/></svg><span>Bholcottlaw.com</span></div>
    </div>
  </header>
  <footer class="footer">
    <div class="footer__address">
      <svg class="icon"><use href="#i-pin"/></svg><span>615 Pemberly St. Ste #300-214, Houston, TX 77002</span><span class="gap"></span>
      <svg class="icon"><use href="#i-phone"/></svg><span>713.555.0187</span><span class="gap"></span>
      <svg class="icon"><use href="#i-fax"/></svg><span>832.555.0129</span>
    </div>
    <div class="footer__divider"></div>
    <div class="footer__label">Letter of Protection</div>
    <div class="page-number">01</div>
  </footer>
</section>

<!-- Option 2: logo left, firm name + minimal stacked contact -->
<section class="sheet sheet--stacked-contact">
  <header class="header header--compact">
    <div class="brand brand--side">
      <div class="brand__mark"></div>
      <div class="brand__name"><span>Bram Holcott</span><span class="brand__sub">Law</span></div>
    </div>
    <div class="contact contact--stacked">
      <div class="contact__item"><span>Law Office of Bram Holcott, PLLC</span><svg class="icon"><use href="#i-office"/></svg></div>
      <div class="contact__item"><span>832.555.0143</span><svg class="icon"><use href="#i-phone"/></svg></div>
      <div class="contact__item"><span>Bholcottlaw.com</span><svg class="icon"><use href="#i-globe"/></svg></div>
    </div>
  </header>
  <footer class="footer">
    <div class="footer__address">
      <svg class="icon"><use href="#i-pin"/></svg><span>615 Pemberly St. Ste #300-214, Houston, TX 77002</span><span class="gap"></span>
      <svg class="icon"><use href="#i-phone"/></svg><span>713.555.0187</span><span class="gap"></span>
      <svg class="icon"><use href="#i-fax"/></svg><span>832.555.0129</span>
    </div>
    <div class="footer__divider"></div>
    <div class="footer__label">Letter of Protection</div>
    <div class="page-number">01</div>
  </footer>
</section>

<!-- Option 3: centered logo, single contact line -->
<section class="sheet sheet--centered">
  <header class="header header--tall">
    <div class="brand brand--center">
      <div class="brand__mark"></div>
      <div class="brand__name"><span>Bram Holcott</span><span class="brand__sub">Law</span></div>
    </div>
    <div class="contact contact--line">
      <div class="contact__item"><svg class="icon"><use href="#i-phone"/></svg><span>832.555.0143</span></div>
      <div class="contact__item"><svg class="icon"><use href="#i-globe"/></svg><span>Bholcottlaw.com</span></div>
    </div>
  </header>
  <footer class="footer">
    <div class="footer__address">
      <svg class="icon"><use href="#i-pin"/></svg><span>615 Pemberly St. Ste #300-214, Houston, TX 77002</span><span class="gap"></span>
      <svg class="icon"><use href="#i-phone"/></svg><span>713.555.0187</span><span class="gap"></span>
      <svg class="icon"><use href="#i-fax"/></svg><span>832.555.0129</span>
    </div>
    <div class="footer__divider"></div>
    <div class="footer__label">Letter of Protection</div>
    <div class="page-number">01</div>
  </footer>
</section>
</body>
</html>
```